Redesign of business card for Cedar Ridge Mechanical

We are looking for a new design for our business cards for Cedar Ridge Mechanical. We are a plumbing & HVAC construction company, operating on the West Coast of Canada and USA. Logo attached.
Industry/Entity Type
Construction - Plumbing & HVAC
Contact Information for Business Card
Name, address, phone numbers, email, website address
Look and feel
Each slider illustrates characteristics of the customer's brand and the style your logo design should communicate.

```html
<!DOCTYPE html>
<html lang="en">
<head>
<meta charset="UTF-8">
<title>Cedar Ridge Mechanical — Business Card</title>
<link href="https://fonts.googleapis.com/css2?family=Poppins:wght@300;400;600&display=swap" rel="stylesheet">
<style>
  :root {
    --backdrop: #222223;
    --card: #1d1d1f;
    --card-back: #262628;
    --ghost: #313133;
    --ink: #ffffff;
    --ink-soft: #e6e6e6;
  }
  * { margin: 0; padding: 0; box-sizing: border-box; }
  html, body {
    width: 1200px; height: 711px; overflow: hidden;
    background: var(--backdrop);
    font-family: "Poppins", sans-serif;
    color: var(--ink);
  }
  .stage {
    position: relative; width: 1200px; height: 711px;
  }
  .card {
    position: absolute;
    width: 520px; height: 300px;
    border-radius: 4px;
    overflow: hidden;
  }
  .card--front {
    left: 50px; top: 205px;
    background: var(--card);
    display: flex; align-items: center; justify-content: center;
  }
  .card--back {
    left: 630px; top: 205px;
    background: var(--card-back);
  }
  .brand {
    display: flex; align-items: center; gap: 14px;
    font-weight: 600; color: var(--ink);
    text-transform: uppercase; letter-spacing: 1px;
  }
  .brand__square {
    background: var(--ink);
    flex: none;
  }
  .card--front .brand { font-size: 27px; }
  .card--front .brand__square { width: 26px; height: 26px; }
  .card--back .brand {
    position: absolute; right: 28px; top: 34px;
    font-size: 13px; gap: 8px;
  }
  .card--back .brand__square { width: 13px; height: 13px; }
  .ghost-mark {
    position: absolute; left: 24px; top: 66px;
    font-size: 64px; font-weight: 600; line-height: 0.95;
    color: var(--ghost); text-transform: uppercase;
    letter-spacing: 2px;
  }
  .holder {
    position: absolute; left: 32px; top: 140px;
    padding-left: 18px;
  }
  .holder__bar {
    position: absolute; left: 0; top: 4px;
    width: 8px; height: 50px; background: var(--ink);
  }
  .holder__name { font-size: 25px; line-height: 1.1; }
  .holder__first { font-weight: 600; }
  .holder__last { font-weight: 300; }
  .holder__title { font-size: 12px; font-weight: 400; color: var(--ink-soft); margin-top: 2px; }
  .address {
    margin-top: 12px; font-size: 11.5px; font-weight: 300; line-height: 1.45;
  }
  .contacts { list-style: none; margin-top: 10px; }
  .contacts li {
    display: flex; align-items: center; gap: 8px;
    font-size: 11.5px; font-weight: 300; line-height: 1.55;
  }
  .contacts svg { width: 12px; height: 12px; flex: none; }
</style>
</head>
<body>
<main class="stage">
  <section class="card card--front" aria-label="Card front">
    <div class="brand"><span class="brand__square"></span>Cedar Ridge Mechanical</div>
  </section>

  <section class="card card--back" aria-label="Card back">
    <div class="ghost-mark" aria-hidden="true">Cedar<br>Ridge</div>
    <div class="brand"><span class="brand__square"></span>Cedar Ridge Mechanical</div>

    <div class="holder">
      <span class="holder__bar"></span>
      <h1 class="holder__name"><span class="holder__first">Marta</span> <span class="holder__last">Kovalenko</span></h1>
      <p class="holder__title">Founder &amp; CEO</p>
      <p class="address">418 Harbour Lane, Suite 12<br>Bellingham, WA 98225</p>
      <ul class="contacts">
        <li>
          <svg viewBox="0 0 24 24" fill="#fff"><path d="M6.6 10.8a15 15 0 0 0 6.6 6.6l2.2-2.2a1 1 0 0 1 1-.25 11.4 11.4 0 0 0 3.6.6 1 1 0 0 1 1 1V20a1 1 0 0 1-1 1A17 17 0 0 1 3 4a1 1 0 0 1 1-1h3.5a1 1 0 0 1 1 1c0 1.25.2 2.45.6 3.6a1 1 0 0 1-.25 1z"/></svg>
          (360) 555-0147
        </li>
        <li>
          <svg viewBox="0 0 24 24" fill="none" stroke="#fff" stroke-width="2"><rect x="3" y="5" width="18" height="14" rx="1"/><path d="M3 6l9 7 9-7"/></svg>
          hello@cedarridgemech.com
        </li>
        <li>
          <svg viewBox="0 0 24 24" fill="none" stroke="#fff" stroke-width="2"><circle cx="12" cy="12" r="9"/><path d="M3 12h18M12 3c3 3.2 3 14.8 0 18M12 3c-3 3.2-3 14.8 0 18"/></svg>
          www.cedarridgemech.com
        </li>
      </ul>
    </div>
  </section>
</main>
</body>
</html>
```